Business Card Design for BrightvaleMedia.com

--I need a business card design for my company BrightvaleMedia.com

I have attached my logo...I want the brightvale media logo on the front of the business card, and then I want The Quillstone Chief on the back of it with my information.

I would like to see a light colored background as well as a dark colored background

FRONT:
BRIGHTVALE MEDIA LOGO
248 N. Larkmoor
3rd Floor
San Diego CA 92173
www.BrightvaleMedia.com

Advanced Website & App Development
Websites, Apps, Online Voucher Systems

Leading Edge Marketing Services
SMS, VB, SMM, SEM,

BACK:
QUILLSTONE CHIEF LOGO
Dorian Pelletta
The Quillstone Chief
Call Or Text: 619-555-0148
Dorian@QuillstoneChief.example
www.QuillstoneChief.example

Target Market(s)

small business owners

Industry/Entity Type

Business Consultant

Contact Information for Business Card

FRONT:
BRIGHTVALE MEDIA LOGO
248 N. Larkmoor
3rd Floor
San Diego CA 92173
www.BrightvaleMedia.com

SMS, VB, SMM, SEM,

BACK:
QUILLSTONE CHIEF LOGO
Dorian Pelletta
The Quillstone Chief
Dorian@QuillstoneChief.example
www.QuillstoneChief.example

Requirements
Must have
• add this quote on it somewhere, anywhere,preferrably on back
• "The Fastest Way To Success Is To Take Action”
• — Dorian Pelletta, Quillstone Chief
Nice to have
• open
Should not have
• red

```html
<!DOCTYPE html>
<html lang="en">
<head>
<meta charset="utf-8">
<title>Brightvale Media — Business Card</title>
<link rel="stylesheet" href="https://fonts.googleapis.com/css2?family=Source+Sans+3:ital,wght@0,400;0,600;1,400&display=swap">
<style>
  :root {
    --backdrop: #4a4a4a;
    --card: #ffffff;
    --brand-blue: #0a6ea8;
    --text-grey: #555555;
    --muted-grey: #777777;
    --band-grey: #6b6b6c;
    --divider: #d4d4d4;
  }
  * { box-sizing: border-box; margin: 0; padding: 0; }
  html, body {
    width: 1105px; height: 1200px; overflow: hidden;
    background: var(--backdrop);
    font-family: "Source Sans 3", "Myriad Pro", sans-serif;
  }
  .stage { position: relative; width: 1105px; height: 1200px; }
  .card {
    position: absolute; left: 192px; width: 720px; height: 412px;
    background: var(--card); overflow: hidden;
  }
  .card--front { top: 146px; }
  .card--back { top: 602px; }

  /* Front */
  .front-content { position: absolute; inset: 0; text-align: center; color: var(--text-grey); }
  .brand-name {
    position: absolute; top: 78px; left: 0; right: 0;
    font-size: 38px; font-weight: 600; letter-spacing: 3px;
    color: var(--brand-blue);
  }
  .address { position: absolute; top: 172px; left: 0; right: 0; font-size: 19px; line-height: 27px; }
  .address .web { color: var(--brand-blue); font-weight: 600; }
  .services { position: absolute; left: 0; right: 0; font-size: 19px; line-height: 27px; }
  .services--dev { top: 262px; }
  .services--marketing { top: 342px; }
  .dot { color: var(--brand-blue); }

  /* Back */
  .sub-brand {
    position: absolute; left: 40px; width: 310px; top: 172px;
    text-align: right; font-size: 30px; font-weight: 600; letter-spacing: 1px;
    color: var(--brand-blue);
  }
  .divider { position: absolute; left: 374px; top: 123px; width: 1px; height: 142px; background: var(--divider); }
  .contact { position: absolute; left: 399px; top: 130px; color: var(--text-grey); }
  .contact-name { font-size: 27px; font-weight: 600; color: var(--brand-blue); line-height: 34px; }
  .contact-title { font-size: 20px; line-height: 26px; }
  .contact-list { list-style: none; margin-top: 22px; font-size: 19px; line-height: 28px; }
  .contact-list li { display: flex; align-items: center; gap: 10px; }
  .contact-list svg { flex: none; fill: var(--brand-blue); }
  .quote {
    position: absolute; left: 0; right: 0; top: 296px;
    text-align: center; color: var(--muted-grey);
  }
  .quote-text { font-size: 17px; font-style: italic; line-height: 23px; }
  .quote-source { font-size: 15px; line-height: 21px; color: var(--brand-blue); }
  .footer-band { position: absolute; left: 0; bottom: 0; }
  .footer-web {
    position: absolute; right: 0; bottom: 0; width: 313px; height: 46px;
    display: flex; align-items: center; justify-content: center;
    color: #ffffff; font-size: 19px; letter-spacing: 1px;
  }
</style>
</head>
<body>
<main class="stage">
  <section class="card card--front" aria-label="Card front">
    <div class="front-content">
      <div class="brand-name">BRIGHTVALE MEDIA</div>
      <p class="address">248 N. Larkmoor, 3rd Floor, San Diego CA 92173<br><span class="web">www.BrightvaleMedia.com</span></p>
      <p class="services services--dev">Advanced Website &amp; App Development<br>Websites <span class="dot">•</span> Apps <span class="dot">•</span> Online Voucher Systems</p>
      <p class="services services--marketing">Leading Edge Marketing Services<br>SMS <span class="dot">•</span> VB <span class="dot">•</span> SMM <span class="dot">•</span> SEM</p>
    </div>
  </section>

  <section class="card card--back" aria-label="Card back">
    <div class="sub-brand">QUILLSTONE CHIEF</div>
    <div class="divider"></div>
    <div class="contact">
      <div class="contact-name">Dorian Pelletta</div>
      <div class="contact-title">The Quillstone Chief</div>
      <ul class="contact-list">
        <li>
          <svg width="16" height="16" viewBox="0 0 24 24" aria-hidden="true"><path d="M6.6 10.8a15.1 15.1 0 0 0 6.6 6.6l2.2-2.2a1 1 0 0 1 1-.25 11.4 11.4 0 0 0 3.6.57 1 1 0 0 1 1 1V20a1 1 0 0 1-1 1A17 17 0 0 1 3 4a1 1 0 0 1 1-1h3.5a1 1 0 0 1 1 1c0 1.25.2 2.45.57 3.57a1 1 0 0 1-.25 1z"/></svg>
          619-555-0148
        </li>
        <li>
          <svg width="16" height="12" viewBox="0 0 16 12" aria-hidden="true"><path d="M0 0h16v1.5L8 7 0 1.5z"/><path d="M0 3.3l8 5.5 8-5.5V12H0z"/></svg>
          Dorian@QuillstoneChief.example
        </li>
      </ul>
    </div>
    <blockquote class="quote">
      <p class="quote-text">“The Fastest Way To Success Is To Take Action”</p>
      <p class="quote-source">— Dorian Pelletta, Quillstone Chief</p>
    </blockquote>
    <svg class="footer-band" width="720" height="46" viewBox="0 0 720 46" aria-hidden="true">
      <rect x="0" y="31" width="380" height="15" fill="var(--band-grey)"/>
      <polygon points="367,46 407,0 720,0 720,46" fill="var(--brand-blue)"/>
    </svg>
    <div class="footer-web">www.QuillstoneChief.example</div>
  </section>
</main>
</body>
</html>
```